Webdesign für Bedrucken Papiertaschen, Schildern etc.
Zielgruppe
Wir bedrucken Papiertaschen, Papierbeutel, Laternen, Aluplaketten, Schilder, etc. und lasern Hundemarken. Zielgruppen von Privat bis Geschäftskunden
Aufgabenstellung
Der Shop sollte ein einfacher und kostengünstiger 'web2print'-shop werden. Wo die Kunden anhand von einem Editor Ihre Logos oder Druckvorlagen selber hochladen und/oder gestalten könne. Bisher haben die Kunden eifach ihre Bidldatei per E-Mail geschickt und wir haben diese dann weiter verarbeit.
Der Shop sollte, wenn möglich, günstig im Unterhalt sein, da wir nicht abschätzen können, wie gut diese laufen wird.
Wir haben wie 3 Bereich: 1. Papierbeutel/Taschen / 2. Stallplaketten (für z.B. Pferdesport) / 3. Diverses (Wie z.B. die Laternen, Schilder, Hundemarken, etc.)
Es würde sich um eine separate Webseite handeln. Daher ist bei Design freie Hand, eifach und klar... auch für nicht so ambitionierte Privatkunden oder kleine Unternehmen.

```html
<!DOCTYPE html>
<html lang="de">
<head>
<meta charset="utf-8">
<title>Tütenwerk – Web-to-Print</title>
<link rel="stylesheet" href="https://fonts.googleapis.com/css2?family=Bricolage+Grotesque:wght@500;600;700&family=Inter:wght@400;500;600&family=JetBrains+Mono:wght@400&display=swap">
<style>
:root{
  --stage:#f5eee4;
  --page:#ffffff;
  --ink:#1d1a17;
  --muted:#7a7168;
  --accent:#c8643a;
  --hero:#fcdcbf;
  --hero-card:#f9e6d2;
  --cream:#f7efe4;
  --cream-2:#efe5d6;
  --line:#e8e0d5;
  --dark:#1f1c1a;
  --kraft:#e3c197;
}
*{box-sizing:border-box;margin:0;padding:0}
html,body{width:1200px;height:3408px;overflow:hidden;background:var(--stage);font-family:"Inter",sans-serif;color:var(--ink)}
.page{position:absolute;left:210px;top:70px;width:780px;height:3269px;background:var(--page);box-shadow:0 20px 60px rgba(60,40,20,.12);overflow:hidden}
.wrap{padding:0 40px}
h1,h2,h3,.display{font-family:"Bricolage Grotesque",sans-serif;letter-spacing:-.02em}
.eyebrow{font-size:7px;letter-spacing:.18em;text-transform:uppercase;color:var(--muted);display:flex;align-items:center;gap:6px;font-weight:500}
.eyebrow::before{content:"";width:14px;height:1px;background:var(--muted)}
.btn{display:inline-flex;align-items:center;gap:6px;border-radius:20px;font-size:9px;font-weight:500;padding:0 14px;height:28px;border:1px solid var(--line);background:#fff;color:var(--ink)}
.btn.dark{background:var(--ink);color:#fff;border-color:var(--ink)}
.btn.orange{background:var(--accent);color:#fff;border-color:var(--accent)}
.btn .circ{width:16px;height:16px;border-radius:50%;border:1px solid currentColor;display:inline-flex;align-items:center;justify-content:center;font-size:8px}
.art{border-radius:6px}
/* header */
.site-header{height:43px;display:flex;align-items:center;padding:0 40px;border-bottom:1px solid var(--line);background:#fff}
.brand{font-family:"Inter",sans-serif;font-weight:700;font-size:15px;display:flex;align-items:center;gap:6px;width:175px}
.brand i{width:9px;height:9px;background:var(--ink);display:inline-block}
.nav{display:flex;gap:20px;font-size:8px;color:var(--muted)}
.nav .on{color:var(--ink);font-weight:600}
.header-actions{margin-left:auto;display:flex;gap:8px;align-items:center}
.header-actions .btn{height:20px;font-size:7.5px;padding:0 10px}
.cart{width:24px;height:24px;border-radius:50%;border:1.5px solid var(--ink);display:flex;align-items:center;justify-content:center}
/* hero */
.hero{height:503px;background:var(--hero);position:relative}
.hero .eyebrow{position:absolute;left:40px;top:72px}
.hero h1{position:absolute;left:40px;top:92px;font-size:44px;line-height:46px;font-weight:600}
.hero h1 em{font-style:normal;color:var(--accent)}
.hero .lead{position:absolute;left:40px;top:286px;width:300px;font-size:10px;line-height:15.5px;color:#4d443c}
.hero .ctas{position:absolute;left:40px;top:352px;display:flex;gap:8px}
.hero .checks{position:absolute;left:40px;top:414px;width:260px;display:flex;flex-wrap:wrap;gap:10px 22px;font-size:7.5px;color:#4d443c}
.checks span{display:flex;align-items:center;gap:5px}
.checks span::before{content:"✓";width:11px;height:11px;border-radius:50%;background:var(--ink);color:#fff;font-size:6px;display:inline-flex;align-items:center;justify-content:center}
.hero-card{position:absolute;left:401px;top:44px;width:339px;height:470px;background:var(--hero-card);border:1px solid #f0cfae;border-radius:10px}
.hero-card .meta{position:absolute;left:28px;top:16px;font-family:"JetBrains Mono",monospace;font-size:6.5px;color:var(--muted);letter-spacing:.1em}
.hero-card .plus{position:absolute;font-size:10px;color:#c9a88a}
.hero-bag{position:absolute;left:120px;top:156px;width:98px;height:120px;background:linear-gradient(180deg,#ecd3b2,#d8b287);border-radius:3px}
/* trust */
.trust{margin:28px 40px 0;height:52px;border:1px solid var(--line);border-radius:8px;display:grid;grid-template-columns:repeat(4,1fr)}
.trust div{display:flex;align-items:center;gap:8px;padding:0 12px;border-right:1px solid var(--line)}
.trust div:last-child{border:0}
.ico{width:20px;height:20px;border-radius:5px;background:var(--cream-2);display:flex;align-items:center;justify-content:center;flex:none}
.trust b{display:block;font-size:7.5px;font-weight:600}
.trust small{font-size:6.5px;color:var(--muted)}
/* sortiment */
.sortiment{margin-top:58px}
.sec-head{display:flex;justify-content:space-between;align-items:flex-end;margin-top:12px}
.sec-head h2{font-size:26px;line-height:28px;font-weight:600}
.sec-head p{width:225px;font-size:8.5px;line-height:13px;color:var(--muted)}
.cats{display:grid;grid-template-columns:290px 200px 200px;gap:5px;margin-top:16px;height:153px}
.cat{border-radius:10px;position:relative;padding:16px;overflow:hidden}
.cat.bags{background:#fcd9bb}
.cat.stall{background:var(--cream);border:1px solid var(--line)}
.cat.misc{background:#ece3d3}
.cat .tag{position:absolute;top:20px;left:16px;background:#fff;border-radius:10px;font-size:6.5px;padding:3px 8px;color:var(--muted)}
.cat .go{position:absolute;top:18px;right:16px;width:24px;height:24px;border-radius:50%;background:var(--ink);color:#fff;font-size:10px;display:flex;align-items:center;justify-content:center}
.cat h3{position:absolute;left:16px;top:72px;font-size:16px;line-height:17px;font-weight:600}
.cat p{position:absolute;left:16px;top:110px;width:170px;font-size:7px;line-height:11px;color:#5c5249}
.cat .pic{position:absolute}
/* steps */
.steps{margin:58px 14px 0;height:355px;background:var(--cream);border-radius:14px;text-align:center;padding-top:60px}
.steps .eyebrow{justify-content:center}
.steps h2{font-size:26px;margin-top:10px;font-weight:600}
.steps .sub{font-size:8.5px;color:var(--muted);width:280px;margin:12px auto 0;line-height:13px}
.step-grid{display:grid;grid-template-columns:repeat(4,1fr);gap:8px;margin:28px 26px 0;text-align:left}
.step{background:#fff;border:1px solid var(--line);border-radius:8px;height:130px;padding:14px;position:relative}
.step .n{font-size:7.5px;color:var(--muted)}
.step .ico{position:absolute;right:14px;top:14px;background:var(--cream)}
.step h3{font-size:11px;margin-top:40px;font-weight:600}
.step p{font-size:7px;line-height:11px;color:var(--muted);margin-top:6px}
/* products */
.products{margin-top:62px}
.prod-grid{display:grid;grid-template-columns:repeat(4,1fr);gap:11px;margin-top:14px}
.prod{border:1px solid var(--line);border-radius:8px;height:193px;overflow:hidden}
.prod .pic{height:125px;background:var(--cream);display:flex;align-items:center;justify-content:center;border-bottom:1px solid var(--line)}
.prod .info{padding:12px 10px}
.prod b{font-size:8px;font-weight:600;display:block}
.prod small{font-size:6.5px;color:var(--muted);display:block;margin-top:3px}
.prod .price{font-size:8px;font-weight:600;margin-top:7px}
.prod .price span{font-weight:400;color:var(--muted);font-size:6.5px}
/* b2b */
.b2b{margin:74px 40px 0;height:334px;background:var(--dark);border-radius:12px;color:#fff;position:relative}
.b2b .eyebrow{position:absolute;left:34px;top:40px;color:var(--accent)}
.b2b .eyebrow::before{background:var(--accent)}
.b2b h2{position:absolute;left:34px;top:56px;font-size:27px;line-height:29px;font-weight:600}
.b2b .txt{position:absolute;left:34px;top:124px;width:270px;font-size:8.5px;line-height:13px;color:#c9c2b8}
.b2b ul{position:absolute;left:34px;top:182px;list-style:none;font-size:8.5px;color:#e6e0d7}
.b2b li{display:flex;align-items:center;gap:8px;height:19.5px}
.b2b li::before{content:"";width:7px;height:7px;border-radius:50%;border:2.5px solid var(--hero)}
.b2b .btn{position:absolute;left:34px;top:272px}
.calc{position:absolute;left:389px;top:63px;width:311px;height:210px;background:#2a2623;border:1px solid #3a3531;border-radius:10px;padding:16px 16px}
.calc .k{font-size:6.5px;letter-spacing:.16em;color:#a59c91;display:flex;align-items:center;gap:5px}
.calc .k::before{content:"";width:4px;height:4px;border-radius:50%;background:#a59c91}
.calc h3{font-size:12px;margin:8px 0 10px;font-weight:600}
.row{display:flex;justify-content:space-between;font-size:7.5px;color:#c9c2b8;padding:6px 0;border-bottom:1px solid #3a3531}
.row.total{border:0;color:#fff;font-weight:600;padding-top:9px}
.row.total span:last-child{font-size:12px}
.calc .cfg{margin-top:12px;height:28px;background:#fff;color:var(--ink);border-radius:16px;font-size:8px;font-weight:500;display:flex;align-items:center;justify-content:center}
/* files */
.files{margin-top:120px;position:relative;height:360px}
.files h2{font-size:26px;line-height:28px;margin-top:12px;font-weight:600}
.files .txt{font-size:8.5px;line-height:13px;color:var(--muted);width:260px;margin-top:12px}
.spec{width:340px;height:37px;background:var(--cream);border-radius:6px;margin-top:9px;display:flex;align-items:center;gap:10px;padding:0 10px}
.spec .ico{background:#fff}
.spec b{font-size:7.5px;font-weight:600;display:block}
.spec small{font-size:6.5px;color:var(--muted)}
.files .first{margin-top:16px}
.files .btn{margin-top:18px;height:24px;font-size:7.5px}
.proof{position:absolute;left:361px;top:46px;width:339px;height:263px;background:var(--cream);border:1px solid var(--line);border-radius:10px}
.proof .fn{position:absolute;left:18px;top:14px;font-family:"JetBrains Mono",monospace;font-size:6.5px;color:var(--muted)}
.proof .sheet{position:absolute;left:24px;top:38px;width:291px;height:177px;background:#fff;border:1px solid #d9cfc2;border-radius:4px}
.proof .sheet::after{content:"";position:absolute;inset:6px;border:1px solid #f0c7b0;border-radius:2px}
.proof .foot{position:absolute;left:18px;right:18px;bottom:14px;display:flex;justify-content:space-between;font-family:"JetBrains Mono",monospace;font-size:6px;color:var(--muted)}
/* faq */
.faq{margin-top:76px;display:flex;justify-content:space-between;height:260px}
.faq-left{width:280px}
.faq-left h2{font-size:26px;line-height:28px;margin-top:12px;font-weight:600}
.faq-left p{font-size:8.5px;line-height:13px;color:var(--muted);margin-top:12px}
.faq-left .btn{margin-top:14px;height:24px;font-size:7.5px}
.faq-list{width:386px;margin-top:-4px}
.q{border-bottom:1px solid var(--line);padding:11px 0;font-size:10px;font-weight:500;display:flex;justify-content:space-between;align-items:flex-start}
.q .pm{width:14px;height:14px;border-radius:50%;border:1px solid var(--line);font-size:9px;display:flex;align-items:center;justify-content:center;color:var(--muted);flex:none}
.q.open .pm{background:var(--ink);color:#fff;border-color:var(--ink)}
.q .a{display:block;font-size:7.5px;line-height:12px;color:var(--muted);font-weight:400;margin-top:8px;width:360px}
/* footer */
.site-footer{position:absolute;left:0;right:0;bottom:0;height:240px;background:var(--cream);padding:38px 40px 0}
.foot-grid{display:flex}
.foot-brand{width:225px}
.foot-brand p{font-size:7.5px;line-height:12px;color:var(--muted);margin-top:12px;width:150px}
.dots{display:flex;gap:3px;margin-top:14px}
.dots i{width:5px;height:5px;border-radius:50%}
.foot-col{width:123px;font-size:7.5px;line-height:19px;color:#4d443c}
.foot-col h4{font-size:6.5px;letter-spacing:.16em;color:var(--muted);font-weight:500;margin-bottom:4px}
.foot-bottom{position:absolute;left:40px;right:40px;bottom:22px;border-top:1px solid var(--line);padding-top:12px;display:flex;justify-content:space-between;font-size:6.5px;color:var(--muted)}
</style>
</head>
<body>
<div class="page">
  <header class="site-header">
    <div class="brand"><i></i>Tütenwerk</div>
    <nav class="nav"><span class="on">Startseite</span><span>Papiertragetaschen</span><span>Stalltafeln</span><span>Sonstiges</span><span>Über uns</span><span>FAQ</span></nav>
    <div class="header-actions">
      <span class="btn"><svg width="8" height="8" viewBox="0 0 10 10"><path d="M1 2h8v5H4L2 9V7H1z" fill="none" stroke="#1d1a17"/></svg>Kontakt</span>
      <span class="cart"><svg width="10" height="10" viewBox="0 0 12 12"><path d="M1 2h2l1.5 6h5.5l1-4H4" fill="none" stroke="#1d1a17" stroke-width="1.2"/></svg></span>
    </div>
  </header>

  <section class="hero">
    <div class="eyebrow">Web-to-Print · Made in Germany</div>
    <h1>Individuell<br>bedruckt.<br><em>In drei Schritten</em><br>bestellt.</h1>
    <p class="lead">Papiertragetaschen, Stalltafeln, Schilder und Gravuren — gestalten Sie Ihr Produkt online, laden Sie Ihre Datei hoch und bestellen Sie ohne Umwege per E-Mail.</p>
    <div class="ctas">
      <span class="btn dark">Jetzt gestalten <span class="circ">→</span></span>
      <span class="btn"><svg width="9" height="9" viewBox="0 0 10 10"><path d="M2 1h4l2 2v6H2z" fill="none" stroke="#1d1a17"/></svg>Dateivorgaben ansehen</span>
    </div>
    <div class="checks"><span>Kein E-Mail-Versand nötig</span><span>Ab 1 Stück bestellbar</span><span>Versand in 3–5 Werktagen</span></div>
    <div class="hero-card">
      <span class="plus" style="left:10px;top:10px">✣</span><span class="plus" style="right:10px;top:10px">✣</span>
      <div class="meta">PROOF · 240 × 320 mm · CMYK</div>
      <div class="hero-bag art" role="img" aria-label="Kraftpapiertasche mit Logo-Platzhalter"></div>
    </div>
  </section>

  <div class="trust">
    <div><span class="ico">⇪</span><span><b>Eigenes Design hochladen</b><small>PDF, JPG, PNG · bis 25 MB</small></span></div>
    <div><span class="ico">⛟</span><span><b>Schneller PaketExpress-Versand</b><small>Versandkostenfrei ab 99 €</small></span></div>
    <div><span class="ico">✓</span><span><b>Qualitätsgarantie</b><small>Kostenlose Druckvorschau</small></span></div>
    <div><span class="ico">◇</span><span><b>ZPR-zertifiziertes Papier</b><small>CO₂-neutraler Versand</small></span></div>
  </div>

  <section class="sortiment wrap">
    <div class="eyebrow">Sortiment</div>
    <div class="sec-head"><h2>Was möchten Sie<br>heute drucken?</h2><p>Drei Hauptbereiche, viele Möglichkeiten. Wählen Sie eine Kategorie und gestalten Sie Ihr Produkt direkt online.</p></div>
    <div class="cats">
      <div class="cat bags"><span class="tag">● 12 Varianten</span><span class="go">→</span><h3>Papiertragetaschen<br>&amp; Papierbeutel</h3><p>Mit eigenem Logo, individuellen Größen — ideal für Boutiquen, Cafés und Events.</p>
        <div class="pic art" role="img" aria-label="Weiße Papiertasche mit Logo" style="left:180px;top:78px;width:70px;height:80px;background:linear-gradient(#fff,#f1ece6)"></div></div>
      <div class="cat stall"><span class="tag">Pferdesport</span><h3>Stalltafeln</h3><p>Robuste Boxenschilder mit Namen &amp; Wappen.</p>
        <div class="pic art" role="img" aria-label="Schwarze Stalltafel mit Pferdename" style="left:108px;top:26px;width:78px;height:52px;background:#1d1a17;border:2px solid #c9a55a"></div></div>
      <div class="cat misc"><span class="tag">Gravur</span><span class="go">→</span><h3>Sonstiges</h3><p>Hundemarken, Schilder, Aluplatten, Laternen.</p>
        <div class="pic" role="img" aria-label="Gravierte Hundemarke" style="left:122px;top:46px;width:58px;height:58px;border-radius:50%;background:radial-gradient(#e9dcbf,#cdb98f)"></div></div>
    </div>
  </section>

  <section class="steps">
    <div class="eyebrow">So funktioniert es</div>
    <h2>In vier Schritten zum fertigen Produkt.</h2>
    <p class="sub">Keine E-Mails, keine Wartezeiten. Alles online, transparent und nachvollziehbar.</p>
    <div class="step-grid">
      <div class="step"><span class="n">01</span><span class="ico">▦</span><h3>Produkt wählen</h3><p>Tasche, Stalltafel oder Schild — wählen Sie Größe, Material und Auflage.</p></div>
      <div class="step"><span class="n">02</span><span class="ico">⇪</span><h3>Design hochladen</h3><p>Eigene Datei (PDF, JPG, PNG) oder im Online-Editor selbst gestalten.</p></div>
      <div class="step"><span class="n">03</span><span class="ico">✓</span><h3>Vorschau prüfen</h3><p>Kostenlose Druckvorschau direkt im Warenkorb — keine Überraschungen.</p></div>
      <div class="step"><span class="n">04</span><span class="ico">⛟</span><h3>Bestellen &amp; erhalten</h3><p>Produktion startet sofort. Lieferung in 3–5 Werktagen per PaketExpress.</p></div>
    </div>
  </section>

  <section class="products wrap">
    <div class="eyebrow">Beliebte Produkte</div>
    <div class="sec-head"><h2 style="font-size:24px">Was unsere Kunden gerade bestellen.</h2><span class="btn" style="height:22px;font-size:7.5px">Alle Produkte ansehen →</span></div>
    <div class="prod-grid">
      <div class="prod"><div class="pic"><div class="art" role="img" aria-label="Kraftpapiertasche" style="width:46px;height:58px;background:linear-gradient(#ecd3b2,#d8b287)"></div></div><div class="info"><b>Papiertragetasche Kraft</b><small>Recyclingpapier · 24 × 30 × 10 cm</small><div class="price">ab 0,89 € <span>/ Stück</span></div></div></div>
      <div class="prod"><div class="pic"><div role="img" aria-label="Hundemarke Knochen" style="width:56px;height:56px;border-radius:50%;background:radial-gradient(#e9dcbf,#cdb98f)"></div></div><div class="info"><b>Hundemarke Knochen</b><small>Edelstahl · Lasergravur</small><div class="price">ab 9,90 € <span>/ Stück</span></div></div></div>
      <div class="prod"><div class="pic"><div class="art" role="img" aria-label="Stalltafel schwarz mit Goldrand" style="width:66px;height:46px;background:#1d1a17;border:2px solid #c9a55a"></div></div><div class="info"><b>Stalltafel Classic</b><small>Aluverbund · 30 × 20 cm</small><div class="price">ab 24,50 € <span>/ Stück</span></div></div></div>
      <div class="prod"><div class="pic"><div class="art" role="img" aria-label="Gebürstetes Aluschild mit Firmenname" style="width:70px;height:42px;background:linear-gradient(90deg,#cfcfcc,#f1f0ec,#c8c7c3)"></div></div><div class="info"><b>Firmenschild Alu</b><small>Aluminium gebürstet · A4</small><div class="price">ab 39,00 € <span>/ Stück</span></div></div></div>
    </div>
  </section>

  <section class="b2b">
    <div class="eyebrow">Geschäftskunden</div>
    <h2>Größere Auflagen?<br>Sprechen Sie mit uns.</h2>
    <p class="txt">Für Vereine, Unternehmen und Veranstalter bieten wir Mengenrabatte ab 500 Stück, individuelle Beratung und Rahmenverträge.</p>
    <ul><li>Staffelpreise mit bis zu 35 % Rabatt</li><li>Persönlicher Ansprechpartner per Telefon</li><li>Rechnung mit 30 Tagen Zahlungsziel</li><li>Lagerhaltung &amp; Nachbestellungen auf Knopfdruck</li></ul>
    <span class="btn orange">Geschäftskundenanfrage →</span>
    <div class="calc">
      <div class="k">BEISPIELKALKULATION</div>
      <h3>1 000 Papiertragetaschen, 4-farbig</h3>
      <div class="row"><span>Einzelpreis</span><span>0,89 €</span></div>
      <div class="row"><span>Druckaufbereitung</span><span>inkl.</span></div>
      <div class="row"><span>Versand</span><span>kostenlos</span></div>
      <div class="row total"><span>Gesamt netto</span><span>890,00 €</span></div>
      <div class="cfg">Konfigurator öffnen</div>
    </div>
  </section>

  <section class="files wrap">
    <div class="eyebrow">Dateivorgaben</div>
    <h2>Druckdaten richtig<br>vorbereiten.</h2>
    <p class="txt">Wir prüfen jede Datei manuell. Falls etwas nicht stimmt, melden wir uns kostenlos — kein Druck startet ohne Ihre Freigabe.</p>
    <div class="spec first"><span class="ico">▢</span><span><b>Format</b><small>PDF/X-4, JPG, PNG, AI · max. 25 MB</small></span></div>
    <div class="spec"><span class="ico">◐</span><span><b>Farbmodus</b><small>CMYK, 300 dpi, Vollfarben möglich</small></span></div>
    <div class="spec"><span class="ico">✂</span><span><b>Beschnitt</b><small>3 mm umlaufend, Sicherheitsabstand 5 mm</small></span></div>
    <div class="spec"><span class="ico">T</span><span><b>Schriften</b><small>In Pfade konvertiert oder eingebettet</small></span></div>
    <span class="btn">Komplette Vorgaben lesen →</span>
    <div class="proof">
      <div class="fn">muster-druckvorlage.pdf</div>
      <div class="sheet"><div class="art" role="img" aria-label="Papiertasche mit Logo-Platzhalter" style="position:absolute;left:118px;top:50px;width:56px;height:70px;background:linear-gradient(#f1dcc0,#e1c29a)"></div></div>
      <div class="foot"><span>BLEED 3mm</span><span>CMYK · 300 dpi</span><span>240 × 320 mm</span></div>
    </div>
  </section>

  <section class="faq wrap">
    <div class="faq-left">
      <div class="eyebrow">Häufige Fragen</div>
      <h2>Wir beantworten<br>die wichtigsten.</h2>
      <p>Antworten auf die Fragen, die unsere Kunden uns am häufigsten stellen. Keine passende dabei? Schreiben Sie uns einfach.</p>
      <span class="btn">Alle Fragen ansehen →</span>
    </div>
    <div class="faq-list">
      <div class="q open"><span>Ab welcher Stückzahl kann ich bestellen?<span class="a">Bei den meisten Produkten ab 1 Stück. Stalltafeln, Hundemarken und Aluschilder sind als Einzelstück verfügbar. Papiertragetaschen drucken wir ab 50 Stück, weil hier die Produktionsumstellung lohnen muss.</span></span><span class="pm">×</span></div>
      <div class="q"><span>Wie lange dauert die Lieferung?</span><span class="pm">+</span></div>
      <div class="q"><span>In welchem Format sollte ich meine Datei hochladen?</span><span class="pm">+</span></div>
      <div class="q"><span>Was kostet der Versand?</span><span class="pm">+</span></div>
      <div class="q"><span>Kann ich eine Druckvorschau bekommen?</span><span class="pm">+</span></div>
    </div>
  </section>

  <footer class="site-footer">
    <div class="foot-grid">
      <div class="foot-brand"><div class="brand"><i></i>Tütenwerk</div><p>Individuell bedruckte Verpackungen, Schilder und Gravuren. Hergestellt in Deutschland.</p><div class="dots"><i style="background:#3a7bd5"></i><i style="background:#d0453a"></i><i style="background:#e6b43a"></i><i style="background:#1d1a17"></i></div></div>
      <div class="foot-col"><h4>SORTIMENT</h4>Papiertragetaschen<br>Papierbeutel<br>Stalltafeln<br>Laternen<br>Hundemarken<br>Aluminiumplatten</div>
      <div class="foot-col"><h4>SERVICE</h4>Dateivorgaben<br>Druckdaten<br>Versand<br>Geschäftskunden<br>FAQ</div>
      <div class="foot-col"><h4>UNTERNEHMEN</h4>Über Tütenwerk<br>Nachhaltigkeit<br>Kontakt<br>Karriere</div>
      <div class="foot-col"><h4>RECHTLICHES</h4>AGB<br>Datenschutz<br>Impressum<br>Widerruf<br>Versandkosten</div>
    </div>
    <div class="foot-bottom"><span>© 2026 Papierhaus GmbH · Hergestellt in Deutschland</span><span>Versandkostenfrei ab 99 € · PaketExpress Grün</span></div>
  </footer>
</div>
</body>
</html>
```